Verdo Consultants Exhibition Booth Design. Cannabis Legal Consultancy

We require a design for the following artwork in PDF of Jpeg high resolution format with these specifications, a 5cm bleed outside and a 10cm safe inside bleed. A tension fabric backdrop 200cm wide and 231cm high. (example loaded) Please see our website www.theverdoconsultants.co.uk
Attached are company logos and head shots for inclusion. You will see our colour schemes from the website. It should announce who we are and provide the company website.

```html
<!DOCTYPE html>
<html lang="en">
<head>
<meta charset="utf-8">
<title>Verdo Consultants – Exhibition Backdrop</title>
<link href="https://fonts.googleapis.com/css2?family=Raleway:wght@500;700;800;900&family=Montserrat:wght@600;700&display=swap" rel="stylesheet">
<style>
  :root {
    --page-bg: #2b2b2b;
    --paper: #f3f4f4;
    --brand-blue: #0a5bb5;
    --deep-navy: #0a1650;
    --mid-blue: #1572d3;
    --steel-grey: #77787b;
    --ink: #222222;
    --white: #ffffff;
  }
  html, body {
    margin: 0;
    padding: 0;
    width: 1200px;
    height: 2206px;
    overflow: hidden;
    background: var(--page-bg);
  }
  .backdrop {
    position: absolute;
    left: 39px;
    top: 618px;
    width: 1122px;
    height: 970px;
    overflow: hidden;
    background: var(--deep-navy);
  }
  .backdrop svg { position: absolute; inset: 0; }
  .brand-name { font-family: "Raleway", sans-serif; font-weight: 500; fill: var(--brand-blue); font-size: 38px; letter-spacing: 1px; }
  .headline { font-family: "Raleway", sans-serif; font-weight: 900; fill: var(--brand-blue); font-size: 70px; }
  .web-address { font-family: "Raleway", sans-serif; font-weight: 800; fill: var(--ink); font-size: 38px; }
  .name-tag { font-family: "Montserrat", sans-serif; font-weight: 700; fill: var(--white); font-size: 14px; }
  .service-label { font-family: "Montserrat", sans-serif; font-weight: 600; fill: var(--white); font-size: 12px; }
  .connect { font-family: "Montserrat", sans-serif; font-weight: 700; fill: var(--white); font-size: 21px; }
</style>
</head>
<body>
<main class="backdrop">
  <svg viewBox="0 0 1122 970" width="1122" height="970" xmlns="http://www.w3.org/2000/svg">
    <defs>
      <radialGradient id="techField" cx="0.75" cy="0.7" r="0.7">
        <stop offset="0" stop-color="#1f86e6"/>
        <stop offset="0.55" stop-color="#0d4fb0"/>
        <stop offset="1" stop-color="#0a1650"/>
      </radialGradient>
      <linearGradient id="portraitLeft" x1="0" y1="0" x2="0" y2="1">
        <stop offset="0" stop-color="#8a8784"/>
        <stop offset="0.45" stop-color="#c9a58f"/>
        <stop offset="0.7" stop-color="#b9b6b2"/>
        <stop offset="1" stop-color="#1c2233"/>
      </linearGradient>
      <linearGradient id="portraitRight" x1="0" y1="0" x2="0" y2="1">
        <stop offset="0" stop-color="#b8ad9f"/>
        <stop offset="0.45" stop-color="#d9a892"/>
        <stop offset="0.72" stop-color="#dfe6ee"/>
        <stop offset="1" stop-color="#161c2c"/>
      </linearGradient>
      <!-- full ring starting at the bottom, running up the left side and over the top -->
      <path id="ringPath" d="M 0 52 A 52 52 0 1 1 0 -52 A 52 52 0 1 1 0 52"/>
    </defs>

    <!-- background tech field -->
    <rect class="tech-pattern" role="img" aria-label="Blue digital grid and binary code pattern" x="0" y="0" width="1122" height="970" fill="url(#techField)"/>

    <!-- sweeping arcs -->
    <path d="M -40 520 Q 200 760 560 800" fill="none" stroke="var(--steel-grey)" stroke-width="22"/>
    <path d="M -40 590 Q 120 760 360 800" fill="none" stroke="var(--white)" stroke-width="16"/>
    <circle cx="380" cy="200" r="557" fill="var(--white)"/>
    <circle cx="380" cy="200" r="533" fill="none" stroke="var(--brand-blue)" stroke-width="26"/>
    <circle cx="380" cy="200" r="511" fill="var(--paper)"/>

    <!-- service trail -->
    <path class="service-trail" d="M 985 -10 C 1040 100, 1070 200, 1033 300 C 1010 380, 1000 420, 960 510 C 920 600, 850 680, 717 755 L 560 790" fill="none" stroke="var(--steel-grey)" stroke-width="30" stroke-linecap="round"/>

    <!-- logo -->
    <g class="logo">
      <circle cx="160" cy="115" r="70" fill="none" stroke="var(--brand-blue)" stroke-width="4"/>
      <text class="brand-name" x="250" y="82">THE</text>
      <text class="brand-name" x="250" y="122">VERDO</text>
      <text class="brand-name" x="250" y="162">CONSULTANTS</text>
    </g>

    <!-- headline -->
    <g class="headline-block">
      <text class="headline" x="92" y="298">ACHIEVING LEGAL</text>
      <text class="headline" x="92" y="362">COMPLIANCE IN</text>
      <text class="headline" x="92" y="426">THE CANNABINOID</text>
      <text class="headline" x="92" y="490">INDUSTRY</text>
      <text class="web-address" x="92" y="558">theverdoconsultants.co.uk</text>
    </g>

    <!-- portraits -->
    <path class="portrait" role="img" aria-label="Portrait photo of Daniel Hart" d="M 100 970 L 100 840 Q 110 760 160 740 L 170 640 Q 200 585 260 590 Q 320 600 330 660 L 330 760 Q 380 790 390 840 L 400 970 Z" fill="url(#portraitLeft)"/>
    <path class="portrait" role="img" aria-label="Portrait photo of Owen Pryce" d="M 330 970 L 350 880 Q 380 830 470 800 L 470 690 Q 480 600 560 595 Q 640 600 650 690 L 650 800 Q 730 830 760 880 L 770 970 Z" fill="url(#portraitRight)"/>

    <!-- name tags -->
    <g class="name-tag-group">
      <circle cx="68" cy="880" r="41" fill="var(--brand-blue)"/>
      <text class="name-tag" x="68" y="877" text-anchor="middle">DANIEL</text>
      <text class="name-tag" x="68" y="893" text-anchor="middle">HART</text>
      <circle cx="663" cy="880" r="41" fill="var(--brand-blue)"/>
      <text class="name-tag" x="663" y="877" text-anchor="middle">OWEN</text>
      <text class="name-tag" x="663" y="893" text-anchor="middle">PRYCE</text>
    </g>

    <!-- services -->
    <g class="service" transform="translate(1020 110)">
      <circle r="66" fill="var(--steel-grey)"/><circle r="42" fill="var(--white)"/>
      <text class="service-label" text-anchor="middle"><textPath href="#ringPath" startOffset="40%">Quality &amp; Control</textPath></text>
      <g fill="none" stroke="var(--brand-blue)" stroke-width="3">
        <line x1="0" y1="-18" x2="0" y2="16"/><line x1="-18" y1="-10" x2="18" y2="-10"/><line x1="-10" y1="18" x2="10" y2="18"/>
        <path d="M -24 4 L -18 -10 L -12 4 Z M 12 4 L 18 -10 L 24 4 Z"/>
      </g>
    </g>
    <g class="service" transform="translate(1033 260)">
      <circle r="66" fill="var(--steel-grey)"/><circle r="42" fill="var(--white)"/>
      <text class="service-label" text-anchor="middle"><textPath href="#ringPath" startOffset="42%">Bespoke Compliance Pathway</textPath></text>
      <g fill="var(--brand-blue)">
        <rect x="-22" y="-10" width="10" height="24"/><rect x="-5" y="-14" width="10" height="28"/><rect x="12" y="-10" width="10" height="24"/>
        <rect x="-24" y="14" width="48" height="4"/>
      </g>
    </g>
    <g class="service" transform="translate(1005 405)">
      <circle r="66" fill="var(--steel-grey)"/><circle r="42" fill="var(--white)"/>
      <text class="service-label" text-anchor="middle"><textPath href="#ringPath" startOffset="40%">Assessment &amp; Advice</textPath></text>
      <circle r="20" fill="var(--brand-blue)"/>
      <path d="M 3 -3 L 3 -24 A 21 21 0 0 1 24 -3 Z" fill="var(--white)" stroke="var(--brand-blue)" stroke-width="2"/>
    </g>
    <g class="service" transform="translate(945 540)">
      <circle r="66" fill="var(--steel-grey)"/><circle r="42" fill="var(--white)"/>
      <text class="service-label" text-anchor="middle"><textPath href="#ringPath" startOffset="38%">Expert Partners</textPath></text>
      <path d="M -26 18 L -4 -8 L 6 4 L 12 -2 L 26 18 Z" fill="var(--brand-blue)"/>
      <line x1="4" y1="-6" x2="4" y2="-24" stroke="var(--brand-blue)" stroke-width="2"/>
      <path d="M 4 -24 L 16 -20 L 4 -16 Z" fill="var(--brand-blue)"/>
    </g>
    <g class="service" transform="translate(848 655)">
      <circle r="66" fill="var(--steel-grey)"/><circle r="42" fill="var(--white)"/>
      <text class="service-label" text-anchor="middle"><textPath href="#ringPath" startOffset="42%">Access to Expert Legal Opinion</textPath></text>
      <circle cx="-8" cy="-6" r="8" fill="var(--brand-blue)"/>
      <path d="M -22 16 Q -8 0 6 16 Z" fill="var(--brand-blue)"/>
      <rect x="4" y="-18" width="20" height="14" fill="none" stroke="var(--brand-blue)" stroke-width="2"/>
    </g>
    <g class="service" transform="translate(717 755)">
      <circle r="66" fill="var(--steel-grey)"/><circle r="42" fill="var(--white)"/>
      <text class="service-label" text-anchor="middle"><textPath href="#ringPath" startOffset="36%">Ongoing Support</textPath></text>
      <circle cy="-6" r="8" fill="var(--brand-blue)"/>
      <path d="M -12 -6 A 12 12 0 0 1 12 -6" fill="none" stroke="var(--brand-blue)" stroke-width="3"/>
      <path d="M -16 18 Q 0 2 16 18 Z" fill="var(--brand-blue)"/>
    </g>

    <!-- connect -->
    <g class="social">
      <text class="connect" x="858" y="877">CONNECT WITH US!</text>
      <circle cx="938" cy="925" r="22" fill="var(--white)"/>
      <circle cx="995" cy="925" r="22" fill="var(--white)"/>
      <circle cx="1052" cy="925" r="22" fill="var(--white)"/>
    </g>
  </svg>
</main>
</body>
</html>
```